International oil and gas consultancy business needs a web design

Hello, I need a web design for a new oil and gas auditing consultancy business. My business undertakes contract audit assignments to review past costs of oil and gas operations (see attached Excel file for more details of the businesses services). I need the design to give the impression of a professional consultancy style of business, rather than a retail style of website. Note: this job is for LAYOUT DESIGN ONLY and not coding / development work.
The following are my key design principles:
1. BASIC DESIGN: I am after a simple and static web design. I don't want the pages busy or cluttered with too many images or detail.
2. HORIZONTAL TABS: I require a horizontal set of tabs towards the top of the screens (see Excel file) which remain in the same position on every page.
3. META TAG PLANNING: The design should allow for effective positioning of content so that key meta tag words can easily be built during the technical build stage.
4. NUMBER OF PAGES: The site will eventually have a maximum of 10 pages. Seven of the pages will reside under the tabs. Can you please present your opening submission for the first two page.
5. USE OF MY LOGO: The attached logo (JPEG file) should be used throughout the website. Please don't change the shape and colour.
6. COLOUR SCHEMES: Can you please consider any of the 3 colour schemes below:
A - dark red (to match the logo), light grey and perhaps another of your liking;
B - dark red (to match the logo), light cream and perhaps another of your liking;
C - dark red (to match the logo), white and perhaps another of your liking.
7. WORD CONTENT: I have attached an Excel file which shows the estimated word content for each page.
8. FUTURE USE OF DESIGN: I'm planning on building a Wordpress website. Can you please ensure the layout design supports this application.

Target Market(s)

oil and gas companies (small and large)

Industry/Entity Type

Oil And Gas

Font styles to use
Sans Serif

Requirements
Nice to have
• The KRL logo and business name should ideally be next to each other. Also, the logo and name should be part of the background graphics, not above it.

```html
<!DOCTYPE html>
<html lang="en">
<head>
<meta charset="utf-8">
<title>KRL – Kingsley Ridge Auditing</title>
<link href="https://fonts.googleapis.com/css2?family=Arimo:wght@400;700&display=swap" rel="stylesheet">
<style>
:root{
  --red:#9b1c1c;
  --nav-top:#c9282c;
  --nav-bottom:#a81c20;
  --text:#555;
  --muted:#888;
  --rule:#e4e4e4;
  --dark:#3a3a3a;
  --btn:#3c3c3c;
  --white:#fff;
}
*{box-sizing:border-box;margin:0;padding:0}
html,body{width:1018px;height:1200px;overflow:hidden;background:var(--white);font-family:"Arimo",Arial,sans-serif;color:var(--text)}
.page{position:relative;width:1018px;height:1200px;border-top:2px solid var(--red)}
.brand{position:absolute;left:112px;top:16px;display:flex;align-items:center;gap:10px}
.brand-mark{width:34px;height:34px;background:var(--red)}
.brand-text{color:var(--red);font-weight:700}
.brand-name{font-size:40px;line-height:40px;letter-spacing:1px;display:block}
.brand-sub{font-size:8px;letter-spacing:.3px;display:block;margin-top:4px}
.social{position:absolute;top:35px;left:567px;display:flex;gap:5px}
.social span{width:24px;height:24px;border-radius:50%;background:#2a6fa8}
.social span:nth-child(2){background:#4ab3e6}
.social span:nth-child(3){background:#333}
.social span:nth-child(4){background:#1f7fa3}
.search{position:absolute;left:700px;top:32px;width:206px;height:32px;border:1px solid #d8d8d8;font-size:10px;color:#999;padding:10px 0 0 11px}
.search svg{position:absolute;right:9px;top:10px}
.nav{position:absolute;left:111px;top:89px;width:795px;height:45px;background:linear-gradient(var(--nav-top),var(--nav-bottom));display:flex}
.nav a{color:var(--white);text-decoration:none;font-size:11.5px;display:flex;align-items:center;justify-content:center;border-right:1px solid #8f161a;box-shadow:1px 0 0 #d4474a}
.nav a:last-child{border:none;box-shadow:none;flex:1}
.hero{position:absolute;left:111px;top:136px;width:795px;height:420px;background:linear-gradient(100deg,#c9d4df 0%,#e9eef3 40%,#2c3445 72%,#d9dfe6 100%)}
.hero-arrows{position:absolute;left:17px;bottom:10px;display:flex;gap:6px}
.hero-arrows span{width:27px;height:26px;background:rgba(90,90,90,.85);display:flex;align-items:center;justify-content:center}
.section-title{position:absolute;left:0;width:1018px;text-align:center;color:var(--red);font-size:18.5px;font-weight:700}
.lead{position:absolute;left:150px;width:718px;text-align:center;font-size:9.8px;line-height:18.5px}
.rule{position:absolute;left:111px;top:683px;width:796px;height:1px;background:var(--rule)}
.card{position:absolute;top:795px;width:254px}
.card-img{height:162px}
.card h3{margin-top:13px;color:var(--red);font-size:14px;font-weight:400}
.card p{margin-top:8px;font-size:9.6px;line-height:18.4px;color:var(--muted)}
.btn{display:inline-block;margin-top:14px;background:var(--btn);color:var(--white);font-size:11.5px;width:96px;height:33px;line-height:33px;text-align:center;box-shadow:0 2px 2px rgba(0,0,0,.25)}
.footer{position:absolute;left:0;top:1123px;width:1018px;height:77px;background:var(--dark)}
.copyright{position:absolute;left:113px;top:34px;font-size:9.6px;color:#ccc}
.footer-social{position:absolute;left:739px;top:27px;display:flex;gap:9px}
.footer-social span{width:27px;height:27px;border-radius:50%;border:2px solid #8a8a8a}
</style>
</head>
<body>
<div class="page">
  <header>
    <div class="brand">
      <span class="brand-mark"></span>
      <span class="brand-text"><span class="brand-name">KRL</span><span class="brand-sub">KINGSLEY RIDGE AUDITING</span></span>
    </div>
    <div class="social" aria-label="Social links"><span></span><span></span><span></span><span></span></div>
    <div class="search">SEARCH
      <svg width="12" height="12" viewBox="0 0 12 12"><circle cx="5" cy="5" r="3.6" fill="none" stroke="#aaa" stroke-width="1.6"/><line x1="7.6" y1="7.6" x2="11" y2="11" stroke="#aaa" stroke-width="2"/></svg>
    </div>
    <nav class="nav">
      <a style="width:84px">HOME</a>
      <a style="width:105px">ABOUT US</a>
      <a style="width:104px">SERVICES</a>
      <a style="width:132px">OUR PARTNERS</a>
      <a style="width:110px">APPROACH</a>
      <a style="width:143px">WHY CHOOSE US</a>
      <a>CONTACT US</a>
    </nav>
  </header>

  <div class="hero" role="img" aria-label="Photo of consultants meeting around an office table with reports">
    <div class="hero-arrows">
      <span><svg width="8" height="12" viewBox="0 0 8 12"><polyline points="6,1 1,6 6,11" fill="none" stroke="#fff" stroke-width="1.6"/></svg></span>
      <span><svg width="8" height="12" viewBox="0 0 8 12"><polyline points="2,1 7,6 2,11" fill="none" stroke="#fff" stroke-width="1.6"/></svg></span>
    </div>
  </div>

  <h1 class="section-title" style="top:585px">WELCOME TO KRL</h1>
  <p class="lead" style="top:623px">Kingsley Ridge Auditing is a Perth (Australia) based firm specialising in providing quality audit services for the oil and gas industry. Our skills and knowledge of oil and gas, along with a deep understanding of business commercial needs, ensures the high quality of our services</p>
  <div class="rule"></div>

  <h2 class="section-title" style="top:701px">OUR SERVICES</h2>
  <p class="lead" style="top:733px">Sed ut perspiciatis unde omnis iste natus error sit voluptatem accusantium doloremque laudantium, totam rem aperiam, eaque ipsa quae ab illo inventore veritatis et quasi architecto beatae vitae dicta sunt explicabo.</p>

  <article class="card" style="left:111px">
    <div class="card-img" role="img" aria-label="Photo of hands working with a calculator and ledger" style="background:linear-gradient(120deg,#2a2a2a,#8a8f98 55%,#e6e8ec)"></div>
    <h3>Joint Venture Audits</h3>
    <p>Sed ut perspiciatis unde omnis iste natus error sit volup-tatem accusantium doloremque laudantium, totam rem architecto beatae vitae dicta sunt explicabo.......</p>
    <span class="btn">READ MORE</span>
  </article>
  <article class="card" style="left:381px">
    <div class="card-img" role="img" aria-label="Photo of a consultant reviewing a contract with clients" style="background:linear-gradient(180deg,#3a3f48,#b9bec6 55%,#1e1e22)"></div>
    <h3>Contract Audits</h3>
    <p>Sed ut perspiciatis unde omnis iste natus error sit volup-tatem accusantium doloremque laudantium, totam rem architecto beatae vitae dicta sunt explicabo.......</p>
    <span class="btn">READ MORE</span>
  </article>
  <article class="card" style="left:651px">
    <div class="card-img" role="img" aria-label="Photo of a magnifying glass over financial charts" style="background:linear-gradient(160deg,#8a93a3,#c08a5a 55%,#e8eaee)"></div>
    <h3>Operations Audits</h3>
    <p>Sed ut perspiciatis unde omnis iste natus error sit volup-tatem accusantium doloremque laudantium, totam rem architecto beatae vitae dicta sunt explicabo.......</p>
    <span class="btn">READ MORE</span>
  </article>

  <footer class="footer">
    <p class="copyright">© Copy Rights&nbsp; 2014 - KRL .All rights reserved</p>
    <div class="footer-social" aria-label="Social links"><span></span><span></span><span></span><span></span><span></span></div>
  </footer>
</div>
</body>
</html>
```